Business Card for Industrial Distributor

We need a business card design for an industrial distributor. We sell machine parts for the manufacturing and oil industry. We would like the cards to look clean and modern but with a touch of industry.

Our colors are blue/white.

Please feel free to visit our website www.korvelpartsco.com

Target Market(s)

mexican manufacturers in the automobile/aerospace industry

Industry/Entity Type

Industrial

Colors
ffffff
0555a3

```html
<!DOCTYPE html>
<html lang="en">
<head>
<meta charset="utf-8">
<title>Korvel business card</title>
<link rel="stylesheet" href="https://fonts.googleapis.com/css2?family=Lato:wght@400;700;900&display=swap">
<style>
  :root {
    --stage: #3b3b3b;
    --white: #ffffff;
    --navy: #2e3192;
    --brand-blue: #2b5ba6;
    --back-light: #2a74b8;
    --back-dark: #2a55a0;
    --grey-text: #8a8a8a;
    --rule: #3a3f94;
  }
  * { box-sizing: border-box; margin: 0; padding: 0; }
  html, body { width: 1200px; height: 810px; overflow: hidden; }
  body {
    background: var(--stage);
    font-family: "Lato", Arial, sans-serif;
    position: relative;
  }
  .card {
    position: absolute;
    top: 250px;
    width: 540px;
    height: 309px;
    overflow: hidden;
  }
  /* back side */
  .card-back {
    left: 40px;
    background: radial-gradient(ellipse at 50% 40%, var(--back-light) 0%, var(--back-dark) 75%);
  }
  .back-brand {
    position: absolute;
    left: 0; right: 0; top: 100px;
    display: flex; align-items: center; justify-content: center; gap: 14px;
  }
  .back-brand .dot {
    width: 40px; height: 40px; border-radius: 50%;
    background: var(--white);
  }
  .back-brand .name {
    font-weight: 900; font-size: 52px; color: var(--white); letter-spacing: 0.5px;
  }
  .back-url {
    position: absolute; left: 0; right: 0; bottom: 40px;
    text-align: center; color: var(--white); font-size: 13px; letter-spacing: 0.3px;
  }
  /* front side */
  .card-front { left: 620px; background: var(--white); }
  .front-brand {
    position: absolute; left: 150px; top: 38px;
    display: flex; align-items: center; gap: 10px;
  }
  .front-brand .dot {
    width: 30px; height: 30px; border-radius: 50%; background: var(--brand-blue);
  }
  .front-brand .name {
    font-weight: 900; font-size: 44px; color: var(--navy); letter-spacing: 0.5px;
  }
  .person {
    position: absolute; left: 140px; top: 128px; width: 210px; text-align: right;
  }
  .person .full-name { font-size: 22px; color: var(--navy); font-weight: 400; }
  .person .role { font-size: 13px; color: var(--grey-text); margin-top: 1px; }
  .company {
    position: absolute; right: 28px; top: 122px; text-align: right; line-height: 1.25;
  }
  .company .legal { font-size: 13px; font-weight: 700; color: var(--navy); }
  .company .address { font-size: 12.5px; color: var(--grey-text); }
  .divider {
    position: absolute; left: 0; right: 0; top: 192px; height: 1.5px; background: var(--rule);
  }
  .contacts {
    position: absolute; left: 40px; top: 203px; list-style: none;
  }
  .contacts li {
    display: flex; align-items: center; gap: 8px;
    font-size: 13px; color: var(--grey-text); line-height: 17px;
  }
  .contacts svg { width: 12px; height: 12px; flex: none; fill: var(--navy); }
  .contacts .web strong { color: var(--navy); font-weight: 400; }
  .band {
    position: absolute; left: 0; right: 0; bottom: 0; height: 26px; background: var(--brand-blue);
  }
</style>
</head>
<body>
  <section class="card card-back" aria-label="Card back">
    <div class="back-brand">
      <span class="dot"></span>
      <span class="name">Korvel</span>
    </div>
    <p class="back-url">www.korvelpartsco.com</p>
  </section>

  <section class="card card-front" aria-label="Card front">
    <div class="front-brand">
      <span class="dot"></span>
      <span class="name">Korvel</span>
    </div>

    <div class="person">
      <p class="full-name">Daniel Reyes</p>
      <p class="role">President &amp; CEO</p>
    </div>

    <div class="company">
      <p class="legal">korvel international Corp.</p>
      <p class="address">4120 Harbor Mill Rd,</p>
      <p class="address">Port Alder, TX 78999</p>
    </div>

    <div class="divider"></div>

    <ul class="contacts">
      <li>
        <svg viewBox="0 0 12 12" aria-hidden="true"><path d="M1 4c0-2 2-3 5-3s5 1 5 3v1H8V3.5H4V5H1zM3 6h6l1.5 5h-9z"/></svg>
        (555) 214 - 7730
      </li>
      <li>
        <svg viewBox="0 0 12 12" aria-hidden="true"><path d="M3 1h6v3H3zM1 5h10v5H9V8H3v2H1zM3.5 9h5v2h-5z"/></svg>
        (555) 214 - 7731
      </li>
      <li>
        <svg viewBox="0 0 12 12" aria-hidden="true"><path d="M1 3h10v6H1zM1.5 3.5L6 7l4.5-3.5" stroke="#fff" stroke-width="0.8"/></svg>
        sales@korvelpartsco.com
      </li>
      <li class="web">
        <svg viewBox="0 0 12 12" aria-hidden="true"><circle cx="6" cy="6" r="5" fill="none" stroke="#2e3192" stroke-width="1"/><ellipse cx="6" cy="6" rx="2.2" ry="5" fill="none" stroke="#2e3192" stroke-width="0.8"/><path d="M1 6h10M2 3.5h8M2 8.5h8" stroke="#2e3192" stroke-width="0.8"/></svg>
        <span>www.<strong>korvelpartsco</strong>.com</span>
      </li>
    </ul>

    <div class="band"></div>
  </section>
</body>
</html>
```